I need a logo design for a new company based in Tucson called "Mindtrail Lee Corwin". I am a psychotherapist that specializes in clinical psychology with athletes and performers. The final design should incorporate the psychology symbol as a watermark. The logo should convey movement and fluidity. "Mindtrail" is a bit of a play on words combining psychology (head) with sports (coach). Other design interests include mid-century, Harold Ames Whitby. I will want to use the logo for business cards, letterhead and marketing brochures. I will put together a website at a later date. I am attaching a file with some pertinent information for the business card. Thank you.
Lee Corwin
mindtrailleecorwin@quillpost.net

Thank you all for the submissions so far.  I have submitted an additional file with a draft of a new design idea.  Since "mindtrail" is a bit of a play on words, I would like to see something with the two "H's" look something like quotation marks.  If the psychology logo is to be included at all, it needs to be less prominent.     Thank you all.  Lee                               

Target Market(s)

1) Adolescent and adult athletes and performers who are looking to increase their level of performance (Sport and Performance Psychology)
2) Adult psychotherapy patients (Clinical psychology)

Industry/Entity Type

Marketing

Colors

Designer to choose colors to be used in the design.

Requirements
Must have
• 1) Since "mindtrail" is a bit of a play on words, The "H's" need to be in a font that looks somewhat like quotation marks.

Nice to have
• Logo on one side. All other info on the backside?

```html
<!DOCTYPE html>
<html lang="en">
<head>
<meta charset="utf-8">
<title>Mindtrail – Business Cards</title>
<link rel="stylesheet" href="https://fonts.googleapis.com/css2?family=Lato:wght@400;700;900&family=Cormorant+Garamond:ital,wght@1,700&display=swap">
<style>
  :root {
    --green: #3a9a47;
    --green-mid: #55b561;
    --green-pale: #a9d8a6;
    --card-white: #fbfbf9;
    --ink: #1c1f1c;
    --backdrop: #e6e7e5;
    --on-green: #ffffff;
  }
  * { margin: 0; padding: 0; box-sizing: border-box; }
  html, body {
    width: 1200px; height: 1000px; overflow: hidden;
    background: var(--backdrop);
    font-family: "Lato", sans-serif;
  }
  .canvas { position: relative; width: 1200px; height: 1000px; }
  .card {
    position: absolute; width: 620px; height: 360px;
    background: var(--card-white);
    overflow: hidden;
    box-shadow: 0 6px 18px rgba(0,0,0,.18);
  }
  .card-front { left: 130px; top: 90px; }
  .card-back { left: 450px; top: 550px; }
  .card-shapes { position: absolute; inset: 0; }

  .brand { position: absolute; }
  .brand-bar {
    display: flex; align-items: center; justify-content: center; gap: 14px;
    background: var(--green);
  }
  .brand-mark { width: 18px; height: 18px; background: var(--ink); }
  .brand-name {
    font-weight: 900; color: var(--ink); letter-spacing: .08em;
    text-transform: uppercase;
  }
  .brand-tagline {
    font-weight: 700; color: var(--ink); text-transform: uppercase;
    letter-spacing: .06em; white-space: nowrap;
  }
  .card-front .brand { left: 170px; top: 95px; width: 390px; }
  .card-front .brand-bar { height: 108px; }
  .card-front .brand-name { font-size: 44px; }
  .card-front .brand-tagline { font-size: 17px; margin-top: 10px; }

  .card-back .brand { left: 32px; top: 135px; width: 240px; }
  .card-back .brand-bar { height: 64px; gap: 10px; }
  .card-back .brand-mark { width: 12px; height: 12px; }
  .card-back .brand-name { font-size: 27px; }
  .card-back .brand-tagline { font-size: 10.5px; margin-top: 7px; }

  .contact {
    position: absolute; left: 300px; top: 40px; width: 300px;
    color: var(--on-green); text-align: center;
  }
  .contact-name {
    font-family: "Cormorant Garamond", serif; font-style: italic; font-weight: 700;
    font-size: 28px; letter-spacing: .02em;
  }
  .contact-role { font-size: 14px; line-height: 1.35; }
  .contact-lines { margin-top: 34px; font-size: 16px; line-height: 1.35; }
  .contact-lines strong { font-weight: 700; }
</style>
</head>
<body>
<main class="canvas">

  <section class="card card-front" aria-label="Card front">
    <svg class="card-shapes" viewBox="0 0 620 360" aria-hidden="true">
      <path d="M0,0 L105,0 C25,110 50,260 210,360 L0,360 Z" fill="var(--green-pale)"/>
      <path d="M0,0 L85,0 C8,115 32,262 182,360 L0,360 Z" fill="var(--green-mid)"/>
      <path d="M0,0 L68,0 C-6,120 18,265 158,360 L0,360 Z" fill="var(--green)"/>
    </svg>
    <div class="brand">
      <div class="brand-bar">
        <span class="brand-mark"></span>
        <span class="brand-name">Mindtrail</span>
      </div>
      <p class="brand-tagline">Clinical &amp; Performance Psychology</p>
    </div>
  </section>

  <section class="card card-back" aria-label="Card back">
    <svg class="card-shapes" viewBox="0 0 620 360" aria-hidden="true">
      <rect width="620" height="360" fill="var(--green)"/>
      <path d="M0,0 L345,0 C250,70 215,230 285,360 L0,360 Z" fill="var(--green-pale)"/>
      <path d="M0,0 L325,0 C232,75 198,232 268,360 L0,360 Z" fill="var(--green-mid)"/>
      <path d="M0,0 L300,0 C210,80 178,235 248,360 L0,360 Z" fill="var(--card-white)"/>
    </svg>
    <div class="brand">
      <div class="brand-bar">
        <span class="brand-mark"></span>
        <span class="brand-name">Mindtrail</span>
      </div>
      <p class="brand-tagline">Clinical &amp; Performance Psychology</p>
    </div>
    <div class="contact">
      <h1 class="contact-name">Lee H. Corwin&nbsp; MA</h1>
      <p class="contact-role">Licensed Professional Counselor</p>
      <p class="contact-role">Clinical &amp; Athletic Performance Psychology</p>
      <div class="contact-lines">
        <p><strong>Mobile:</strong> 520.555.0148</p>
        <p><strong>Fax:</strong> 520.555.0192</p>
        <p><strong>Email:</strong> mindtrailleecorwin@quillpost.net</p>
        <p><strong>Address:</strong> 4120 East Alder #210 Tucson,<br>AZ 85712</p>
      </div>
    </div>
  </section>

</main>
</body>
</html>
```